Bright Nook Home Page (A Home Wellness e-commerce site & blog)

We need a dynamic home page created for a home wellness brand. Must be visually appealing and extremely mobile-friendly. Logos and a Navmap have been provided but that is just a guideline, PLEASE USE YOUR CREATIVITY.

Target Market(s)

1st target demo: females 24-48, 2nd target demo: all 24-48

Number of Pages Required

1 page

```html
<!DOCTYPE html>
<html lang="en">
<head>
<meta charset="utf-8">
<title>Bright Nook — Home Wellness</title>
<link rel="stylesheet" href="https://fonts.googleapis.com/css2?family=Open+Sans:wght@300;400;600&family=Tinos:wght@400;700&display=swap">
<style>
:root{
  --teal:#2fb6bd;
  --teal-soft:#3fbcc3;
  --purple:#45197f;
  --ink:#333333;
  --muted:#555555;
  --footer:#1c1719;
  --white:#ffffff;
}
*{box-sizing:border-box;margin:0;padding:0}
html,body{width:1200px;height:3342px;overflow:hidden}
body{position:relative;background:var(--white);font-family:"Open Sans",Arial,sans-serif;color:var(--ink)}
.serif{font-family:"Tinos","Times New Roman",serif;font-weight:700}
.abs{position:absolute}

.promo-bar{left:0;top:0;width:1200px;height:44px;background:var(--teal);color:var(--white);font-family:"Tinos",serif;font-size:13px;text-align:center;line-height:40px}
.cart-icon{left:1040px;top:8px}

.site-nav{left:0;top:44px;width:1200px;height:90px;background:var(--purple)}
.brand{left:132px;top:22px;font-size:32px;font-weight:400;color:var(--white);letter-spacing:-.5px}
.nav-link{top:37px;font-size:13px;font-weight:600;color:var(--white);text-decoration:none;transform:translateX(-50%)}
.nav-link.active{color:var(--teal)}
.nav-smile{left:396px;top:62px}
.social{display:flex;gap:6px}
.social span{width:17px;height:17px;background:var(--white);border-radius:3px;display:block}

.hero{left:0;top:134px;width:1200px;height:700px;background:linear-gradient(180deg,#c9c6c3 0%,#e2e0dc 35%,#b9c0c2 58%,#d8cbbd 70%,#e6d9ca 100%)}
.hero-card{left:132px;top:320px;width:352px;height:331px;background:rgba(255,255,255,.92);border:1px solid #e6e6e6}
.hero-card::before{content:"";position:absolute;inset:8px;border:2px solid #e2e2e2}
.hero-title{top:50px;width:100%;text-align:center;font-size:44px;color:var(--teal)}
.hero-sub{top:126px;width:100%;text-align:center;font-size:24px;font-weight:300;line-height:30px;color:#444}
.btn-solid{background:var(--teal);color:var(--white);font-family:"Tinos",serif;font-weight:700;text-align:center;text-decoration:none;display:block}
.hero-cta{left:79px;top:217px;width:194px;height:51px;font-size:19px;line-height:51px}
.slider-arrow{top:489px;width:44px;height:44px;border-radius:50%;background:rgba(200,200,200,.55)}

.sale-band{left:0;top:800px;width:1200px}
.sale-text{left:0;top:876px;width:1200px;text-align:center;color:var(--white);font-size:37px;line-height:44px}

.section-title{width:1200px;left:0;text-align:center;color:var(--purple);font-size:38px}
.tile{position:absolute}

.about{left:0;top:1942px;width:1200px;height:436px;background:linear-gradient(100deg,#3cb9c0,#49c3c8 50%,#37b1b8)}
.about-title{top:72px;width:1200px;text-align:center;color:var(--white);font-size:42px}
.about-copy{left:190px;top:156px;width:820px;text-align:center;color:var(--white);font-size:17px;line-height:27px}
.btn-outline{left:488px;top:303px;width:224px;height:50px;border:3px solid var(--white);color:var(--white);font-size:20px;line-height:44px;text-align:center;text-decoration:none}

.blog-sub{left:0;top:2482px;width:1200px;text-align:center;font-size:14px;color:var(--muted)}
.post{top:2532px;width:288px}
.post-image{width:288px;height:145px}
.post-title{margin-top:20px;font-size:18px;line-height:23px;color:var(--teal)}
.post-body{margin-top:8px;font-size:12px;line-height:22px;color:#444}
.post-btn{margin-top:30px;width:148px;height:40px;font-size:18px;line-height:40px}

.footer{left:0;top:2981px;width:1200px;height:361px;background:var(--footer);color:var(--white)}
.footer-brand{left:132px;top:98px;font-size:26px;font-weight:400}
.footer-social{left:132px;top:188px}
.footer-social span{width:24px;height:24px}
.footer-head{top:75px;font-size:15px}
.footer-list{top:121px;list-style:none;font-size:12px;line-height:30px}
.newsletter-copy{left:779px;top:114px;width:292px;font-size:11px;line-height:22px}
.newsletter-field{left:784px;top:188px;width:284px;height:38px;border:1px solid #555;font-size:13px;color:#aaa;padding-left:16px;line-height:36px}
.newsletter-field svg{position:absolute;right:16px;top:13px}
.footer-rule{left:132px;top:298px;width:936px;height:1px;background:#3a3436}
.copyright{left:0;top:320px;width:1200px;text-align:center;font-size:11px}
</style>
</head>
<body>

<div class="abs promo-bar">Free shipping on all orders $50 and over!</div>
<svg class="abs cart-icon" width="28" height="28" viewBox="0 0 28 28" aria-label="Cart">
  <path d="M9 9V7a5 5 0 0 1 10 0v2" fill="none" stroke="#fff" stroke-width="1.5"/>
  <rect x="3" y="9" width="22" height="17" rx="2" fill="none" stroke="#fff" stroke-width="1.5"/>
  <text x="14" y="22" text-anchor="middle" font-size="10" fill="#fff" font-family="Tinos,serif">0</text>
</svg>

<header class="abs site-nav">
  <div class="abs brand">BrightNook</div>
  <a class="abs nav-link active" style="left:414px">Home</a>
  <svg class="abs nav-smile" width="40" height="12" viewBox="0 0 40 12"><path d="M3 3 Q20 16 37 3" fill="none" stroke="#2fb6bd" stroke-width="3" stroke-linecap="round"/></svg>
  <a class="abs nav-link" style="left:479px">Sale</a>
  <a class="abs nav-link" style="left:578px">Featured Product</a>
  <a class="abs nav-link" style="left:694px">About Us</a>
  <a class="abs nav-link" style="left:782px">Payment</a>
  <a class="abs nav-link" style="left:856px">Blog</a>
  <a class="abs nav-link" style="left:927px">Contact</a>
  <div class="abs social" style="left:978px;top:36px"><span></span><span></span><span></span><span></span></div>
</header>

<section class="abs hero" role="img" aria-label="Woman in a yoga tree pose on a sandy beach with dune grass under a cloudy sky"></section>
<div class="abs slider-arrow" style="left:40px"></div>
<div class="abs slider-arrow" style="left:1114px"></div>
<svg class="abs" style="left:40px;top:489px" width="44" height="44"><path d="M26 12 L18 22 L26 32" fill="none" stroke="#fff" stroke-width="1.5"/></svg>
<svg class="abs" style="left:1114px;top:489px" width="44" height="44"><path d="M18 12 L26 22 L18 32" fill="none" stroke="#fff" stroke-width="1.5"/></svg>

<div class="abs hero-card">
  <h1 class="abs serif hero-title">Bright Nook</h1>
  <p class="abs hero-sub">We are a Home Wellness<br>company</p>
  <a class="abs btn-solid hero-cta">SHOP NOW</a>
</div>

<svg class="abs sale-band" width="1200" height="204" viewBox="0 0 1200 204">
  <path d="M0 0 Q600 70 1200 0 V204 H0 Z" fill="#2fb6bd"/>
  <path d="M0 18 Q600 82 1200 18 V204 H0 Z" fill="#45197f"/>
</svg>
<p class="abs serif sale-text">50% off sale going on now! Because saving<br>money also makes us happy</p>

<h2 class="abs serif section-title" style="top:1068px">Featured Product</h2>
<div class="tile" role="img" aria-label="Person with raised arms on a rock at sunset" style="left:218px;top:1167px;width:252px;height:220px;background:linear-gradient(180deg,#4d8fd0,#e8c66b 60%,#3a2a1a)"></div>
<div class="tile" role="img" aria-label="Stack of smooth stones on a pebble beach" style="left:475px;top:1167px;width:252px;height:220px;background:linear-gradient(180deg,#bcd9dc,#8fc3c4 45%,#a59d92)"></div>
<div class="tile" role="img" aria-label="Woman relaxing with eyes closed" style="left:731px;top:1167px;width:252px;height:443px;background:linear-gradient(120deg,#e4e0dc,#d9b6a0 55%,#2d2a2a)"></div>
<div class="tile" role="img" aria-label="Woman receiving a face massage at a spa" style="left:218px;top:1391px;width:252px;height:219px;background:linear-gradient(160deg,#7f9a55,#c7a081 50%,#ece8e1)"></div>
<div class="tile" role="img" aria-label="Woman leaping on a beach at sunset" style="left:475px;top:1391px;width:252px;height:219px;background:linear-gradient(180deg,#f0b26d,#f3c888 50%,#c88a5c)"></div>
<div class="tile" role="img" aria-label="Grey stones and bamboo leaves on white sand" style="left:218px;top:1614px;width:252px;height:220px;background:linear-gradient(135deg,#6aa348 0%,#e9e9e8 30%,#efefee)"></div>
<div class="tile" role="img" aria-label="Woman with arms raised toward a sunset sky" style="left:475px;top:1614px;width:252px;height:220px;background:linear-gradient(180deg,#6f9ecb,#d6c2a6 70%,#e8b26a)"></div>
<div class="tile" role="img" aria-label="Aromatherapy oil bottles and a candle on a wooden table" style="left:731px;top:1614px;width:252px;height:220px;background:linear-gradient(180deg,#d9a98a,#b47a5a 60%,#e7e3df)"></div>

<section class="abs about" aria-label="About Us">
  <h2 class="abs serif about-title">About Us</h2>
  <p class="abs about-copy">They say that home is where the heart is. But home is also where your mind and body reside. At Bright Nook we believe that home should be your place of Zen. A respite from the crazy world outside those walls. It is where you recharge your soul so you can approach each day with the focus and energy necessary to conquer the world.</p>
  <a class="abs serif btn-outline">TELL ME MORE</a>
</section>

<h2 class="abs serif section-title" style="top:2424px">The Happy Blog</h2>
<p class="abs blog-sub">Food for the mind, tips for the body and exercises for the soul</p>

<article class="abs post" style="left:132px">
  <div class="post-image" role="img" aria-label="Group doing push-ups outdoors on grass" style="background:linear-gradient(180deg,#d4d8c8,#a9b58a 60%,#6f8f3a)"></div>
  <h3 class="serif post-title">Finibus Bonorum et Malorum the Extremes of Good.</h3>
  <p class="post-body">Temporibus autem quibusdam et aut officiis debitis aut rerum necessitatibus saepe eveniet ut et voluptates repudiandae sint et molestiae non recusandae.</p>
  <a class="btn-solid post-btn">LEARN MORE</a>
</article>
<article class="abs post" style="left:456px">
  <div class="post-image" role="img" aria-label="Hands preparing a fresh green salad in a bowl" style="background:linear-gradient(180deg,#cfcbc4,#d8c34a 45%,#5d7a36 75%,#eae6e0)"></div>
  <h3 class="serif post-title">Excepteur sint occaecat cupidatat non proident</h3>
  <p class="post-body">Temporibus autem quibusdam et aut officiis debitis aut rerum necessitatibus saepe eveniet ut et voluptates repudiandae sint et molestiae non recusandae.</p>
  <a class="btn-solid post-btn">LEARN MORE</a>
</article>
<article class="abs post" style="left:780px">
  <div class="post-image" role="img" aria-label="Woman with open arms by a lake at sunrise" style="background:linear-gradient(180deg,#6f8aa0,#c9b59a 50%,#4d5c66)"></div>
  <h3 class="serif post-title">Dignissimos ducimus qui blanditiis praesentium</h3>
  <p class="post-body">Temporibus autem quibusdam et aut officiis debitis aut rerum necessitatibus saepe eveniet ut et voluptates repudiandae sint et molestiae non recusandae.</p>
  <a class="btn-solid post-btn">LEARN MORE</a>
</article>

<footer class="abs footer">
  <div class="abs footer-brand">BrightNook</div>
  <div class="abs social footer-social"><span></span><span></span><span></span><span></span></div>

  <h4 class="abs serif footer-head" style="left:377px">Company</h4>
  <ul class="abs footer-list" style="left:379px"><li>Home</li><li>Sale</li><li>Featured Product</li><li>About Us</li><li>Payment</li></ul>

  <h4 class="abs serif footer-head" style="left:594px">Help</h4>
  <ul class="abs footer-list" style="left:595px"><li>Blog</li><li>Terms of Use</li><li>Privacy Policy</li><li>Site Map</li><li>Contact</li></ul>

  <h4 class="abs serif footer-head" style="left:777px">Sign up for our newsletter</h4>
  <p class="abs newsletter-copy">At vero eos et accusamus et iusto odio dignissimos ducimus qui blanditiis praesentium voluptatum deleniti atque corrupti quos dolores et quas molestias.</p>
  <div class="abs newsletter-field">Enter Your Email
    <svg width="12" height="10" viewBox="0 0 12 10"><rect width="12" height="10" rx="1" fill="#2fb6bd"/><path d="M0 1 L6 6 L12 1" fill="none" stroke="#1c1719" stroke-width="1.2"/></svg>
  </div>
  <div class="abs footer-rule"></div>
  <p class="abs copyright">© 2021 YourBrightNook . All rights reserved.</p>
</footer>

</body>
</html>
```